Commercial Real Estate Appraisal Company needs a postcard design

We need a postcard design for a commercial real estate company based out of Ballston Lake, New York called "Harborline Appraisers".

Harborline Appraisers, LLC., provides high quality commercial appraisal and real estate consulting services to our clients. Our company provides appraisal services for financial lending institutions, real estate developers, local municipalities, attorney’s, private individuals and businesses. Significant capital expenditures were made to ensure we can provide top of the line data research and research publications, as well as, generate our reports with industry leading appraisal software for increased accuracy and efficiency.

Services we provide

Advisory & Consulting Services, Net Lease Valuation, Capitalization Rate Consultation, Operating Expense Consultation, Discounted Cash Flow Analysis, Portfolio Valuation, Expert Witness Services, Property and Comparable Analyses, Financial Feasibility Studies, Property Tax Services, Going Concern Valuations, Real Estate Due Diligence Analyses, Highest and Best Use Studies, Real Estate Valuation, Lease Versus Purchase Analyses, Rent Arbitration and Consultation, Market Rent Analyses, Sale Lease-Backs Analysis, Market Studies, Site Inspections, Divorce Proceedings, Probate / Estate Matters

Please save room on the card for postage and addressing

Industry/Entity Type

Real Estate

```html
<!DOCTYPE html>
<html lang="en">
<head>
<meta charset="utf-8">
<title>Harborline Appraisers – Postcard</title>
<link rel="stylesheet" href="https://fonts.googleapis.com/css2?family=Cinzel:wght@500&family=Arimo:ital@1&display=swap">
<style>
  :root {
    --paper: #ffffff;
    --navy: #1b2040;
    --ink: #151515;
    --rule: #222222;
    --mark: #2a3158;
  }
  * { margin: 0; padding: 0; box-sizing: border-box; }
  html, body { width: 1200px; height: 778px; overflow: hidden; background: var(--paper); }
  .postcard {
    position: relative;
    width: 1200px;
    height: 778px;
    background: var(--paper);
  }
  .brand-mark {
    position: absolute;
    left: 70px;
    top: 60px;
    width: 150px;
    height: 150px;
    border-radius: 50%;
    background: var(--mark);
  }
  .brand {
    position: absolute;
    left: 248px;
    top: 34px;
    width: 722px;
    text-align: center;
    color: var(--navy);
    font-family: "Cinzel", serif;
    font-weight: 500;
  }
  .brand-name {
    font-size: 54px;
    line-height: 60px;
    letter-spacing: 0.5px;
  }
  .brand-tagline {
    margin-top: 2px;
    font-size: 19px;
    letter-spacing: 4.2px;
    text-transform: uppercase;
  }
  .stamp-box {
    position: absolute;
    left: 1006px;
    top: 17px;
    width: 177px;
    height: 176px;
    border: 2px solid var(--rule);
  }
  .about {
    position: absolute;
    left: 26px;
    top: 348px;
    width: 790px;
    font-family: "Arimo", sans-serif;
    font-style: italic;
    font-size: 25.5px;
    line-height: 31px;
    color: var(--ink);
  }
  .address-line {
    position: absolute;
    height: 0;
    border-top: 2px solid var(--rule);
  }
  .address-line--short { left: 880px; width: 234px; }
  .address-line--long { left: 813px; width: 354px; }
</style>
</head>
<body>
  <main class="postcard">
    <div class="brand-mark" aria-hidden="true"></div>

    <header class="brand">
      <h1 class="brand-name">Harborline Appraisers</h1>
      <p class="brand-tagline">Real Estate Appraisers &amp; Consultants</p>
    </header>

    <div class="stamp-box" aria-label="Postage stamp area"></div>

    <p class="about">
      Our company provides high quality commercial appraisal<br>
      and real estate consulting services to our clients. Our com-<br>
      pany provides appraisal services for financial lending insti-<br>
      tutions, real estate developers, local municipalities,<br>
      attorney’s, private individuals and businesses. Significant<br>
      capital expenditures were made to ensure we can provide<br>
      top of the line data research and research publications, as<br>
      well as, generate our reports with industry leading appraisal<br>
      software for increased accuracy and efficiency.
    </p>

    <div class="address-block" aria-label="Mailing address lines">
      <div class="address-line address-line--short" style="top:387px"></div>
      <div class="address-line address-line--long" style="top:447px"></div>
      <div class="address-line address-line--long" style="top:497px"></div>
      <div class="address-line address-line--long" style="top:547px"></div>
      <div class="address-line address-line--long" style="top:596px"></div>
      <div class="address-line address-line--long" style="top:646px"></div>
    </div>
  </main>
</body>
</html>
```